Classic and neutral book cover design

We are looking for a classic and neutral book cover design to be used as the template for a series of books to be published. We are hence looking for a template that will allow us to easily change the title name for all books in this series.
The use of very few colours (black and white is welcome) and few design elements is a big bonus. As a source of inspiration we would like to ask you to view the very simple and
If you think you have a cool idea that can add a twist to the formal classic look don't hesitate. Go for it !
Work will be done for a 30 year old Sweden based cultural non-profit called VĂ©ru (www.verufoundation.example). We work with the publishing and supporting of post-modern art and literature addressing contemporary topics but are also involved in assisting projects of cultural preservation.
Target Market(s)
The audience is expected to have some form of interest in culture but could range from hobbyist readers to tenure track scholars
Industry/Entity Type
Non-Profit
Requirements
Must have
- General:
- Classic and neutral feel
- Preferably very simple and few shapes
- usage of few colours (black and white is welcome)
Information to be displayed on the cover is:
- Author
- Title
- type of work e.g. play/novel (optional)
- publishing house (in this case "Veru Publishing")
Nice to have
- ideas to prevent it from become boring are of course welcome
Should not have
- - too many colours

```html
<!DOCTYPE html>
<html lang="en">
<head>
<meta charset="utf-8">
<title>Nice Title — Veru Publishing</title>
<link rel="stylesheet" href="https://fonts.googleapis.com/css2?family=EB+Garamond:ital,wght@0,400;0,500;1,400&display=swap">
<style>
  :root {
    --paper: #ffffff;
    --frame: #b29c7c;
    --ink: #1c1c1c;
    --title: #f07d90;
    --art-light: #ebe6dd;
    --art-warm: #efd6d6;
  }
  * { box-sizing: border-box; margin: 0; padding: 0; }
  html, body {
    width: 952px;
    height: 1200px;
    overflow: hidden;
    background: var(--paper);
  }
  .cover {
    position: relative;
    width: 952px;
    height: 1200px;
    background: var(--paper);
    font-family: "EB Garamond", Garamond, serif;
    color: var(--ink);
  }
  .frame {
    position: absolute;
    border: 3px solid var(--frame);
  }
  .frame--outer { left: 42px; top: 42px; right: 40px; bottom: 34px; }
  .frame--inner { left: 57px; top: 57px; right: 55px; bottom: 49px; }

  .publisher {
    position: absolute;
    top: 180px;
    left: 0;
    width: 100%;
    text-align: center;
    font-style: italic;
    font-size: 18px;
    letter-spacing: 0.2em;
    text-transform: uppercase;
  }
  .title {
    position: absolute;
    top: 318px;
    left: 0;
    width: 100%;
    text-align: center;
    font-weight: 400;
    font-size: 88px;
    line-height: 1;
    letter-spacing: 0.2em;
    padding-left: 0.2em;
    color: var(--title);
    text-transform: uppercase;
  }
  .cover-art {
    position: absolute;
    left: 377px;
    top: 504px;
    width: 200px;
    height: 200px;
    border-radius: 50%;
    background: linear-gradient(135deg, var(--art-light), var(--art-warm));
  }
  .credits {
    position: absolute;
    top: 784px;
    left: 0;
    width: 100%;
    text-align: center;
  }
  .credits__type {
    font-style: italic;
    font-size: 27px;
    line-height: 1;
  }
  .credits__by {
    margin-top: 30px;
    font-style: italic;
    font-size: 19px;
    line-height: 1;
  }
  .credits__author {
    margin-top: 20px;
    font-size: 31px;
    line-height: 1;
    letter-spacing: 0.16em;
    padding-left: 0.16em;
  }
</style>
</head>
<body>
  <main class="cover">
    <div class="frame frame--outer"></div>
    <div class="frame frame--inner"></div>

    <p class="publisher">Veru Publishing</p>
    <h1 class="title">Nice Title</h1>

    <div class="cover-art" role="img" aria-label="Round abstract painting of loose brush strokes in cream, pink, rose and tan"></div>

    <div class="credits">
      <p class="credits__type">Novel</p>
      <p class="credits__by">by</p>
      <p class="credits__author">Author Authorson</p>
    </div>
  </main>
</body>
</html>
```